Vellisant - Quality health delivered at your door

Vellisant offers home and Community Based Services for adults who wish to continue live independently in their communities. We increase accessibility to health care, reduce health care delivery gap, reduce mortality and morbidity, reduce health while promoting healthy living in the comfort of our patients communities or homes.

We provide on site services and deliver high quality healthcare at your door. Our experienced physicians coordinate care with our certified nurse practitioners and provide chronic care management, physical therapy, rehabilitation and medications management.

Target Market(s)

Older population living in independent living facilities

Industry/Entity Type

Health Care

Contact Information for Business Card

Vellisant

Number of Pages Required

4 page

Font styles to use
Sans Serif

Colors

Designer to choose colors to be used in the design.

```html
<!DOCTYPE html>
<html lang="en">
<head>
<meta charset="utf-8">
<title>Vellisant – Quality health delivered at your door</title>
<link rel="stylesheet" href="https://fonts.googleapis.com/css2?family=Open+Sans:wght@400;600;700&display=swap">
<style>
:root{
  --orange:#f7941d;
  --green-dark:#1a3300;
  --green-deep:#132700;
  --ink:#2b2b2b;
  --muted:#555;
  --grey-panel:#f0f0f0;
  --line:#e2e2e2;
  --white:#fff;
}
*{box-sizing:border-box;margin:0;padding:0}
html,body{width:697px;height:1200px;overflow:hidden}
body{position:relative;background:var(--white);font-family:"Open Sans",Arial,sans-serif;color:var(--ink)}
.abs{position:absolute}

/* header */
.top-links{top:17px;right:80px;display:flex;gap:16px;font-size:7px;color:#444;letter-spacing:.2px}
.nav-bar{top:47px;left:0;width:697px;height:34px;background:var(--orange)}
.nav-bar ul{list-style:none;display:flex;gap:17px;position:absolute;left:175px;top:12px;font-size:7.4px;color:#fff8ec}
.nav-bar li.active{font-weight:700;color:#fff}
.brand-tab{top:0;left:57px;width:109px;height:100px;background:#fff;box-shadow:0 1px 3px rgba(0,0,0,.15);clip-path:polygon(0 0,100% 0,100% 92%,50% 100%,0 92%)}
.brand-mark{position:absolute;left:34px;top:10px;width:40px;height:40px;border-radius:50%;background:var(--orange);border:2px solid var(--green-dark)}
.brand-name{position:absolute;left:0;width:100%;top:60px;text-align:center;font-size:13px;font-weight:400;color:var(--green-dark);letter-spacing:.3px}

/* hero */
.hero{top:81px;left:0;width:697px;height:291px;background:linear-gradient(90deg,#2c8fa3 0%,#d8b49a 30%,#e9e3dc 55%,#c9bfb4 75%,#3d95b8 100%)}
.hero-title{top:256px;left:75px;font-size:17.6px;line-height:21px;font-weight:700;color:#fff;text-transform:uppercase;text-shadow:0 1px 3px rgba(0,0,0,.35)}
.btn{background:var(--orange);color:#fff;font-weight:700;font-size:7.6px;text-transform:uppercase;display:flex;align-items:center;justify-content:center;letter-spacing:.2px}
.hero-btn{top:305px;left:76px;width:72px;height:18px}
.hero-arrows{top:332px;left:90px}

/* welcome */
.welcome-title{top:389px;left:0;width:697px;text-align:center;font-size:13px;font-weight:700}
.welcome-title::after{content:"";display:block;width:30px;height:2px;background:var(--orange);margin:5px auto 0}
.welcome-text{top:421px;left:100px;width:497px;text-align:center;font-size:6.6px;line-height:12px;color:var(--muted)}
.welcome-btn{top:464px;left:313px;width:72px;height:18px}

/* services */
.services-photo{top:503px;left:0;width:349px;height:292px;background:linear-gradient(135deg,#e9edf0 0%,#f4f2ee 45%,#d9d2c6 80%,#b7a894 100%)}
.services-panel{top:503px;left:349px;width:348px;height:292px;background:var(--grey-panel)}
.services-title{top:538px;left:378px;font-size:12px;color:#222}
.services-list{top:563px;left:378px;list-style:none;font-size:7.5px;color:#333}
.services-list li{height:15px;line-height:15px;padding-left:10px;position:relative}
.services-list li::before{content:"";position:absolute;left:0;top:4px;border-left:4px solid #333;border-top:3px solid transparent;border-bottom:3px solid transparent}

/* enroll */
.enroll-title{top:852px;left:80px;font-size:17px;color:#333}
.enroll-note{top:878px;left:80px;width:120px;font-size:7.4px;line-height:11.5px;font-weight:600;color:#444}
.email-field{top:910px;left:80px;width:114px;height:18px;border:1px solid #ddd;font-size:6.8px;color:#333;padding:4px 6px}
.email-field svg{position:absolute;right:6px;top:5px}
.join-btn{top:931px;left:80px;width:57px;height:17px;font-size:7.6px}
.pager{top:959px;left:80px;display:flex;gap:3px}
.pager span{width:13px;height:12px;background:#eee;border:1px solid #ddd;display:flex;align-items:center;justify-content:center}
.card{top:850px;width:128px;height:162px;border:1px solid var(--line);background:#fff}
.card-photo{height:90px}
.card h3{font-size:8px;font-weight:400;color:#222;margin:8px 6px 3px;line-height:11px}
.card p{font-size:6.4px;line-height:12px;color:#555;margin:0 6px;text-align:justify}

/* footer */
.footer{top:1024px;left:0;width:697px;height:176px}
.footer-col-title{font-size:12px;color:var(--orange)}
.footer-brand-mark{top:1042px;left:75px;width:36px;height:36px;border-radius:50%;background:var(--orange);border:2px solid #fff}
.footer-brand-name{top:1078px;left:58px;font-size:11px;color:#fff}
.footer-about{top:1099px;left:58px;width:140px;font-size:7px;line-height:12px;color:#fff}
.links{top:1085px;left:226px;width:92px;list-style:none;font-size:7px;color:#ddd}
.links li{height:24px;line-height:24px;border-bottom:1px dashed #6b7d55;padding-left:15px;position:relative}
.links li::before{content:"›";position:absolute;left:2px}
.t-arrows{top:1063px;left:453px;display:flex;gap:2px}
.t-arrows span{width:9px;height:9px;background:#777}
.avatar{top:1081px;left:347px;width:32px;height:32px;border-radius:50%;background:linear-gradient(#c9c3bb,#8d857c);border:2px solid #fff}
.t-name{top:1084px;left:388px;font-size:8px;font-weight:700;color:var(--orange)}
.t-role{top:1096px;left:388px;font-size:6.4px;color:var(--orange);font-style:italic}
.t-quote{top:1117px;left:346px;width:130px;font-size:6.4px;line-height:12px;color:#ccc;text-align:justify}
.contact{top:1082px;left:500px;width:131px;font-size:6.4px;color:#ddd}
.contact div{position:relative;padding-left:12px;border-bottom:1px dashed #6b7d55;padding-bottom:6px;margin-bottom:6px;line-height:11.5px}
.contact svg{position:absolute;left:0;top:2px}
.footer-bar{top:1176px;left:0;width:697px;height:24px;background:var(--green-deep);border-top:1px solid #2c4512;text-align:center;font-size:6.4px;line-height:23px;color:#bbb}
</style>
</head>
<body>

<header>
  <nav class="abs top-links"><span>REHABILITATION</span><span>MEMORA LEARNING CENTER</span><span>MEMORA LEARNING®</span><span>CONTACT US</span></nav>
  <nav class="abs nav-bar">
    <ul><li class="active">Home</li><li>Assisted Living</li><li>Skilled Nursing</li><li>Independent Living</li><li>Home and Community Based Services</li><li>Respite Care</li></ul>
  </nav>
  <div class="abs brand-tab"><span class="brand-mark"></span><span class="brand-name">VELLISANT</span></div>
</header>

<section>
  <div class="abs hero" role="img" aria-label="Smiling caregiver in teal scrubs greeting an elderly woman"></div>
  <h1 class="abs hero-title">Vellisant offers home and<br>community based services</h1>
  <div class="abs btn hero-btn">Learn more</div>
  <svg class="abs hero-arrows" width="30" height="16" viewBox="0 0 30 16"><path d="M8 2 3 8l5 6M20 2l5 6-5 6" fill="none" stroke="#ffffff" stroke-opacity=".7" stroke-width="1.2"/></svg>
</section>

<section>
  <h2 class="abs welcome-title">WELCOME</h2>
  <p class="abs welcome-text">Vellisant offers home and Community Based Services for adults who wish to continue to live independently in the comfort of their communities. We provide on site services and deliver high quality healthcare at your door. Our experienced physicians coordinate care with our certified nurse practitioners and provide chronic care management, physical therapy, rehabilitation and medications management.</p>
  <div class="abs btn welcome-btn">Read more</div>
</section>

<section>
  <div class="abs services-photo" role="img" aria-label="Nurse serving tea to a smiling senior woman at a table"></div>
  <div class="abs services-panel"></div>
  <h2 class="abs services-title">OUR SERVICES</h2>
  <ul class="abs services-list">
    <li>Comprehensive primary care services</li>
    <li>Coordination of speciality care</li>
    <li>Chronic disease management such as COPD, Asthma, Diabetes</li>
    <li>mellitus, Heart disease like congestive heart failure, Alzheimer’s</li>
    <li>dementia, etc...</li>
    <li>Transitional Care</li>
    <li>Skilled nursing visits for wound care, catheter care, ostomy</li>
    <li>Social services assessment</li>
    <li>Home health assistance</li>
    <li>Physical therapy</li>
    <li>Mental health</li>
    <li>Dental health</li>
    <li>Transportation</li>
  </ul>
</section>

<section>
  <h2 class="abs enroll-title">Enroll Today</h2>
  <p class="abs enroll-note">(Membership Request to Join items here)</p>
  <div class="abs email-field">Enter Email id
    <svg width="8" height="6" viewBox="0 0 8 6"><rect x=".5" y=".5" width="7" height="5" fill="none" stroke="#333" stroke-width=".8"/><path d="M.5.5 4 3.5 7.5.5" fill="none" stroke="#333" stroke-width=".8"/></svg>
  </div>
  <div class="abs btn join-btn">JOIN NOW</div>
  <div class="abs pager">
    <span><svg width="4" height="6"><path d="M3.5.5 1 3l2.5 2.5" fill="none" stroke="#333"/></svg></span>
    <span style="background:#ccc"><svg width="4" height="6"><path d="M.5.5 3 3 .5 5.5" fill="none" stroke="#333"/></svg></span>
  </div>

  <article class="abs card" style="left:215px">
    <div class="card-photo" role="img" aria-label="Caregiver helping an elderly man in a wheelchair" style="background:linear-gradient(135deg,#e8e6e3,#b9c5c9 60%,#8fa3aa)"></div>
    <h3>Chronic care management</h3>
    <p>Neque porro quisquam est, qui dolorem ipsum quia dolor sit amet, consectetur,</p>
  </article>
  <article class="abs card" style="left:354px">
    <div class="card-photo" role="img" aria-label="Therapist exercising with a senior woman by a window" style="background:linear-gradient(135deg,#eef1ee,#c8d9b4 55%,#9fb98a)"></div>
    <h3>Physical therapy</h3>
    <p>Neque porro quisquam est, qui dolorem ipsum quia dolor sit amet, consectetur,</p>
  </article>
  <article class="abs card" style="left:493px">
    <div class="card-photo" role="img" aria-label="Nurse giving medication to a seated elderly woman" style="background:linear-gradient(135deg,#b98e6f,#d9a79a 50%,#e8cfc4)"></div>
    <h3>Rehabilitation &amp; medications management</h3>
    <p>Neque porro quisquam est, qui dolorem ipsum quia dolor ....</p>
  </article>
</section>

<footer>
  <svg class="abs footer" width="697" height="176" viewBox="0 0 697 176"><path d="M0 0Q348 22 697 0V176H0Z" fill="var(--green-dark)"/></svg>
  <span class="abs footer-brand-mark"></span>
  <div class="abs footer-brand-name">VELLISANT</div>
  <p class="abs footer-about">Lorem ipsum dolor sit amet, consectetur adipiscing elit, sed do eiusmod tempor incididunt ut labore et dolore magna aliqua.</p>

  <h3 class="abs footer-col-title" style="top:1060px;left:226px">Useful Links</h3>
  <ul class="abs links"><li>Privacy Policy</li><li>Terms &amp; Conditions</li><li>Sitemap</li></ul>

  <h3 class="abs footer-col-title" style="top:1060px;left:346px">Testimonials</h3>
  <div class="abs t-arrows"><span></span><span></span></div>
  <div class="abs avatar" role="img" aria-label="Portrait of the reviewer"></div>
  <div class="abs t-name">Marek Olsen</div>
  <div class="abs t-role">CEO</div>
  <p class="abs t-quote">Lorem ipsum dolor sit amet, consectetur adipiscing elit, sed do eiusmod tempor incididunt ut labore et...</p>

  <h3 class="abs footer-col-title" style="top:1060px;left:500px">Contact</h3>
  <div class="abs contact">
    <div><svg width="7" height="9" viewBox="0 0 7 9"><path d="M3.5 8.5S.5 5 .5 3.3a3 3 0 0 1 6 0C6.5 5 3.5 8.5 3.5 8.5Z" fill="none" stroke="#999"/></svg>123 Building name, Area, City,<br>Country, Zipcode.</div>
    <div><svg width="8" height="8" viewBox="0 0 8 8"><path d="M1 1h2l1 2-1 1a5 5 0 0 0 2 2l1-1 2 1v2C4 8 0 4 1 1Z" fill="#999"/></svg>+ 12 (34) 555 0142</div>
    <div style="border:none"><svg width="9" height="7" viewBox="0 0 9 7"><rect x=".5" y=".5" width="8" height="6" fill="none" stroke="#999"/><path d="M.5.5 4.5 4 8.5.5" fill="none" stroke="#999"/></svg>info@vellisant.com</div>
  </div>

  <div class="abs footer-bar">Copyright © 2017 www.vellisant-care.com &nbsp;|&nbsp; All Rights Reserved.</div>
</footer>

</body>
</html>
```